Kestrel Home Business Card Design

We need a business card for a Building company based in Queensland, Australia. Our colours are orange black and we do base all our homes design names and other aspect of our business on astrology. We want the consumer to perceive the company as professional and to attract investors to our company.We have over 20 years in the building industry.We pride ourselves on our innovation of designs and making the building process for anyone from families to investor a smooth and simple experience.
Business
Amelia Prichard0411752116PO Box 454, Mudgeerbaameliaprichard@zodiachomes.com

```html
<!DOCTYPE html>
<html lang="en">
<head>
<meta charset="utf-8">
<title>Kestrel Homes – Business Card</title>
<link rel="stylesheet" href="https://fonts.googleapis.com/css2?family=Alegreya:wght@400;700&display=swap">
<style>
  :root {
    --backdrop: #ece9e4;
    --card-black: #0b0b0b;
    --card-glow: #1c1a19;
    --orange: #f28c1e;
    --white: #f4f2ef;
    --shadow: rgba(0, 0, 0, 0.28);
  }
  * { box-sizing: border-box; margin: 0; padding: 0; }
  html, body {
    width: 1200px;
    height: 900px;
    overflow: hidden;
    background: var(--backdrop);
    font-family: "Alegreya", Georgia, serif;
  }
  .canvas {
    position: relative;
    width: 1200px;
    height: 900px;
  }
  .card {
    position: absolute;
    width: 560px;
    height: 320px;
    background: radial-gradient(ellipse at 50% 40%, var(--card-glow) 0%, var(--card-black) 70%);
    box-shadow: 0 14px 30px var(--shadow);
    color: var(--white);
  }
  .card--back { left: 90px; top: 100px; }
  .card--front { left: 550px; top: 480px; }

  /* back face */
  .back-mark {
    position: absolute;
    inset: 0;
    display: flex;
    flex-direction: column;
    align-items: center;
    justify-content: center;
    gap: 18px;
  }
  .back-mark .dot {
    width: 120px;
    height: 120px;
    border-radius: 50%;
    background: var(--orange);
  }
  .brand-name {
    font-weight: 700;
    color: var(--white);
    letter-spacing: 0.5px;
    white-space: nowrap;
  }
  .back-mark .brand-name { font-size: 30px; }

  /* front face */
  .front-brand {
    position: absolute;
    right: 28px;
    top: 24px;
    display: flex;
    flex-direction: column;
    align-items: flex-end;
    gap: 10px;
  }
  .front-brand .dot {
    width: 62px;
    height: 62px;
    border-radius: 50%;
    background: var(--orange);
    margin-right: 72px;
  }
  .front-brand .brand-name { font-size: 28px; }

  .holder {
    position: absolute;
    left: 34px;
    top: 146px;
  }
  .holder-name { font-size: 30px; font-weight: 400; line-height: 1.1; }
  .holder-role { font-size: 17px; color: var(--orange); margin-top: 2px; }

  .contact {
    position: absolute;
    left: 34px;
    top: 222px;
    font-size: 16px;
    line-height: 1.6;
    font-style: normal;
    white-space: nowrap;
  }
  .contact .label { color: var(--orange); }
  .contact .web { color: var(--orange); }
  .contact .gap { margin-left: 8px; }
</style>
</head>
<body>
<main class="canvas">

  <section class="card card--back" aria-label="Business card, back">
    <div class="back-mark">
      <span class="dot"></span>
      <span class="brand-name">Kestrel Homes</span>
    </div>
  </section>

  <section class="card card--front" aria-label="Business card, front">
    <div class="front-brand">
      <span class="dot"></span>
      <span class="brand-name">Kestrel Homes</span>
    </div>

    <div class="holder">
      <h1 class="holder-name">Harriet Colvane</h1>
      <p class="holder-role">Managing Director</p>
    </div>

    <address class="contact">
      <div>PO Box 872, Larkspur Ridge, Country, 00000</div>
      <div>
        <span class="label">T:</span> (07) 5550 4418
        <span class="label gap">F:</span> (07) 5550 4419
        <span class="label gap">M:</span> 0491 570 110
      </div>
      <div>
        <span class="label">E:</span> info@kestrelhomes.example
        <span class="web gap">www.kestrelhomes.example</span>
      </div>
    </address>
  </section>

</main>
</body>
</html>
```